Creation of an elegant and modern turnkey Shopify website

Hello,

We are a new company specializing in the sale of above-ground pools. We want to create a turnkey website, ideally using Shopify. For now, we need a "showcase" site, not an e-commerce platform, with four tabs:

Home Page (an overall presentation of the company)
Our Products (an overview of all the above-ground pools we sell)
Our Projects (a page inspired by Instagram to showcase photos of our future projects)
Contact (a page with all our contact information and a contact form)

We are looking to create a highly visual, elegant, and modern website with vibrant splashes of color. We will provide the text, photos (along with instructions on where to place them on each page), and all other necessary information as attachments.

Thank you in advance for your proposals!

The Brisa Lagoon Team

Target Market(s)

Targeted at Swiss customers (a translator will need to be installed for different languages)

Industry/Entity Type

Sale of customised above-ground pools

Coding

Coded - Design and coding required

Font styles to use
Sans Serif

Colors
0094D4
00A9DD
6FCCEA
C7EBF8
E9F6FB
00AB8E
00BBA5
67D7C9
C6EFE9
E9F9F6

Requirements
Must have
• A stunning, elegant and modern look
Nice to have
• Inspiration from the colors of our logo throughout the site, but in an elegant way
Should not have
• An overly classic look for swimming pool sites

```html
<!DOCTYPE html>
<html lang="en">
<head>
<meta charset="utf-8">
<title>Brisa Lagoon – Above-Ground Pools</title>
<link href="https://fonts.googleapis.com/css2?family=Baloo+2:wght@500;600&family=Lato:wght@300;400;700&display=swap" rel="stylesheet">
<style>
:root{
  --cyan:#03e6fa;
  --cyan-btn:#08e3f6;
  --ink:#111111;
  --muted:#333333;
  --grey-logo:#8a8a8a;
  --water-deep:#1c8fa3;
  --water:#47b8c8;
  --water-light:#9fdde6;
  --stone:#a78f7a;
  --line:#cfcfcf;
  --white:#ffffff;
}
*{margin:0;padding:0;box-sizing:border-box}
html,body{width:1200px;height:3055px;overflow:hidden;background:var(--white)}
body{position:relative;font-family:"Lato",sans-serif;color:var(--ink)}
.abs{position:absolute}
h1,h2,h3{font-family:"Baloo 2",sans-serif;font-weight:600;line-height:1.15}
.btn{position:absolute;background:var(--cyan-btn);color:#0b2a33;font-family:"Lato",sans-serif;font-size:16px;font-weight:400;display:flex;align-items:center;justify-content:center;text-decoration:none}

/* header */
.site-header{position:absolute;left:0;top:0;width:1200px;height:100px}
.brand{position:absolute;font-family:"Lato",sans-serif;font-weight:300;color:var(--grey-logo);line-height:0.95;letter-spacing:1px}
.brand--head{left:114px;top:18px;font-size:30px}
.main-nav{position:absolute;left:450px;top:44px;display:flex;gap:32px;font-family:"Baloo 2",sans-serif;font-weight:500;font-size:15px}
.main-nav a{color:var(--ink);text-decoration:none}
.header-tools{position:absolute;left:893px;top:43px;display:flex;gap:18px;align-items:center}
.header-tools svg{width:22px;height:22px}
.lang{font-family:"Baloo 2",sans-serif;font-size:15px;display:flex;align-items:center;gap:6px}

/* hero */
.hero{position:absolute;left:0;top:100px;width:1200px;height:561px;
  background:linear-gradient(90deg,var(--stone) 0 8%,transparent 8% 93%,var(--stone) 93%),
  linear-gradient(160deg,var(--water-light),var(--water) 45%,var(--water-deep))}
.hero-welcome{position:absolute;left:116px;top:132px;font-size:28px;color:var(--white);font-weight:400}
.hero-title{position:absolute;left:110px;top:180px;font-family:"Lato",sans-serif;font-weight:700;font-size:72px;color:var(--white);letter-spacing:1px}
.hero-sub{position:absolute;left:107px;top:262px;width:470px;font-size:30px;color:var(--white);font-weight:600;line-height:1.4}
.hero .btn{left:111px;top:367px;width:149px;height:49px}

/* intro */
.intro-title{left:111px;top:738px;width:460px;font-size:37px}
.intro-text{left:111px;top:892px;width:445px;font-size:13px;line-height:28px;color:var(--muted)}
.photo{position:absolute}

/* features */
.why-title{left:114px;top:1192px;font-size:37px}
.feature{position:absolute;top:1290px;width:170px}
.feature svg{width:56px;height:56px;stroke:var(--ink);fill:none;stroke-width:1.6}
.feature h3{font-family:"Lato",sans-serif;font-weight:700;font-size:15px;margin:24px 0 12px}
.feature p{font-size:11.5px;line-height:19px;color:var(--muted)}

/* personalized band */
.service-band{position:absolute;left:111px;top:1566px;width:978px;height:389px;
  background:linear-gradient(90deg,#2b3b33 0 16%,#2a8ea6 40%,#4ab6cc 75%,#8ea6a2)}
.service-band h2{position:absolute;left:43px;top:60px;color:var(--white);font-size:38px}
.service-band p{position:absolute;left:42px;top:120px;width:420px;color:var(--white);font-weight:700;font-size:15.5px;line-height:25px}
.service-band .btn{left:51px;top:268px;width:148px;height:49px}

/* satisfaction */
.sat-title{left:668px;top:2036px;font-size:37px}
.sat-text{left:668px;top:2102px;width:440px;font-size:13px;line-height:28.5px;color:var(--muted)}

/* contact band */
.contact-band{position:absolute;left:0;top:2424px;width:1200px;height:318px;background:var(--cyan);text-align:center}
.contact-band h2{margin-top:48px;font-size:37px}
.contact-band p{margin:18px auto 0;width:620px;font-size:15.5px;line-height:27.5px;color:#14323a}
.contact-band .tagline{font-family:"Lato",sans-serif;font-weight:700;font-size:25px;margin-top:36px;color:var(--ink)}

/* footer */
.brand--foot{left:110px;top:2858px;font-size:50px}
.foot-links{position:absolute;top:2858px;list-style:none;font-size:12.5px;line-height:25px}
.foot-links a{color:var(--ink);text-decoration:none}
.newsletter{position:absolute;left:812px;top:2852px;width:277px}
.newsletter strong{font-size:12.5px;font-weight:700}
.news-field{margin-top:34px;border-bottom:1px solid var(--ink);display:flex;justify-content:space-between;padding-bottom:6px;font-size:12.5px}
.foot-rule{left:111px;top:2998px;width:978px;height:1px;background:var(--line)}
.copyright{left:112px;top:3016px;font-size:11.5px;color:#555}
.socials{position:absolute;left:927px;top:3012px;display:flex;gap:6px}
.socials span{width:28px;height:28px;display:block}
</style>
</head>
<body>

<header class="site-header">
  <div class="brand brand--head">BRISA<br>LAGOON</div>
  <nav class="main-nav">
    <a href="#">Home</a><a href="#">Our Products</a><a href="#">Our Works</a><a href="#">Contact Us</a>
  </nav>
  <div class="header-tools">
    <svg viewBox="0 0 24 24" fill="none" stroke="#111" stroke-width="1.8"><circle cx="10" cy="10" r="7"/><path d="M15 15l6 6"/></svg>
    <svg viewBox="0 0 24 24" fill="none" stroke="#111" stroke-width="1.6"><circle cx="12" cy="8" r="4"/><path d="M5 21v-3a5 5 0 0 1 5-5h4a5 5 0 0 1 5 5v3z"/></svg>
    <svg viewBox="0 0 24 24" fill="none" stroke="#111" stroke-width="1.6"><path d="M12 20s-8-5-8-11a4 4 0 0 1 8-1 4 4 0 0 1 8 1c0 6-8 11-8 11z"/></svg>
    <span class="lang"><svg viewBox="0 0 24 24" fill="none" stroke="#111" stroke-width="1.4"><circle cx="12" cy="12" r="9"/><path d="M3 12h18M12 3c3 3 3 15 0 18M12 3c-3 3-3 15 0 18"/></svg>Eng
      <svg viewBox="0 0 24 24" style="width:14px;height:14px" fill="none" stroke="#111" stroke-width="3"><path d="M4 8l8 8 8-8"/></svg></span>
  </div>
</header>

<section class="hero">
  <div class="abs" role="img" aria-label="Aerial view of a rectangular turquoise pool with a pineapple float and steps" style="inset:0"></div>
  <p class="hero-welcome">Welcome To</p>
  <h1 class="hero-title">BRISA LAGOON</h1>
  <p class="hero-sub">Transform Your Garden with Our Premium Above-Ground Pools!</p>
  <a class="btn" href="#">Discover Now</a>
</section>

<h2 class="abs intro-title">Achieve Your Dreams With Our Custom, Tailor-Made Above-Ground Pools.</h2>
<p class="abs intro-text">Imagine an exceptional relaxation and leisure space right in your own backyard. With our unparalleled expertise and commitment to excellence, we create above-ground pools that exceed all expectations. Our exclusive, custom-designed models are crafted to combine style, durability, and innovation, offering a unique and refined experience.</p>
<a class="btn" href="#" style="left:111px;top:1066px;width:148px;height:49px">Read More</a>
<div class="photo" role="img" aria-label="Woman floating on a pink ring in clear pool water" style="left:617px;top:747px;width:245px;height:368px;background:linear-gradient(160deg,#cfeff2,#8fd3dc 60%,#b8e6ea)"></div>
<div class="photo" role="img" aria-label="Legs of a swimmer in a turquoise sun hat by the pool" style="left:870px;top:747px;width:245px;height:368px;background:linear-gradient(170deg,#5cc7d8,#9fe0ea 55%,#3fb7c8)"></div>

<h2 class="abs why-title">Why Choose Our Above-Ground Pools?</h2>
<div class="feature" style="left:110px">
  <svg viewBox="0 0 56 56"><circle cx="24" cy="22" r="16"/><path d="M24 12l3 6 6 1-4.5 4 1 6-5.5-3-5.5 3 1-6-4.5-4 6-1z"/><path d="M14 34l-5 12 7-2 3 6 4-11M34 34l5 12-7-2-3 6-4-11"/></svg>
  <h3>Superior Quality</h3>
  <p>Each pool is constructed with high-quality materials, ensuring exceptional durability and strength.</p>
</div>
<div class="feature" style="left:313px">
  <svg viewBox="0 0 56 56"><path d="M4 24L28 4l24 20"/><path d="M18 14v22M30 14v22M18 22h12M18 30h12"/><path d="M4 40q6-4 12 0t12 0 12 0 12 0M4 47q6-4 12 0t12 0 12 0 12 0"/></svg>
  <h3>Elegant Design</h3>
  <p>2.Our pools come in a variety of styles and finishes, seamlessly blending into any garden setting.</p>
</div>
<div class="feature" style="left:516px">
  <svg viewBox="0 0 56 56"><path d="M6 6v44h44"/><path d="M14 42l26-26 6 6-26 26H14z"/><path d="M36 20l6 6M42 40h8v8"/></svg>
  <h3>Custom and Tailor-Made</h3>
  <p>3. Create the pool of your dreams with our customization options, tailored to your specific tastes and needs.</p>
</div>
<div class="feature" style="left:719px">
  <svg viewBox="0 0 56 56"><path d="M28 4l5 5 7-1 2 7 6 4-3 6 3 6-6 4-2 7-7-1-5 5-5-5-7 1-2-7-6-4 3-6-3-6 6-4 2-7 7 1z"/><circle cx="28" cy="28" r="11"/><path d="M23 28l4 4 7-8"/></svg>
  <h3>Easy Installation</h3>
  <p>4.Enjoy your new oasis quickly with our simple and fast installation process.</p>
</div>
<div class="feature" style="left:922px">
  <svg viewBox="0 0 56 56"><path d="M19 36a14 14 0 1 1 18 0v6H19z"/><path d="M21 46h14M23 50h10"/><circle cx="28" cy="24" r="6"/><path d="M28 2v4M8 24H4M52 24h-4M13 9l3 3M43 9l-3 3"/></svg>
  <h3>Constant Innovation</h3>
  <p>We incorporate the latest technologies to provide you with an optimal and safe swimming experience.</p>
</div>

<section class="service-band">
  <div class="abs" role="img" aria-label="Aerial view of a garden pool with a swimmer on a blue float" style="inset:0"></div>
  <h2>Personalized Services</h2>
  <p>We understand that every garden and client is unique. That's why we offer personalized services, from design to installation and after-sales support. Our team of experts is here to answer all your questions and guide you throughout your project.</p>
  <a class="btn" href="#">Read More</a>
</section>

<div class="photo" role="img" aria-label="Hot tub on a wooden deck in a green garden" style="left:109px;top:2042px;width:247px;height:292px;background:linear-gradient(180deg,#4f7a3b 0 25%,#cfe7ef 40%,#707070 70%,#8a7b6a)"></div>
<div class="photo" role="img" aria-label="Children with sunglasses smiling at the pool edge" style="left:363px;top:2042px;width:245px;height:292px;background:linear-gradient(180deg,#2bb6d8,#5fd0ea 55%,#e9b49a)"></div>
<h2 class="abs sat-title">Guaranteed Satisfaction</h2>
<p class="abs sat-text">Your satisfaction is our top priority. We are committed to providing you with exceptional service and the highest quality products. Join our community of satisfied customers who are already enjoying their custom above-ground pools. 10-Year Warranty!</p>
<a class="btn" href="#" style="left:667px;top:2250px;width:148px;height:49px">Read More</a>

<section class="contact-band">
  <h2>Contact Us Today</h2>
  <p>Don't wait any longer to transform your garden into a wellness oasis. Contact us today to discover our range of customizable above-ground pools and get a tailored quote. Dive into a world of infinite possibilities with [Your Company Name].</p>
  <p class="tagline">We Bring Your Pool Dreams to Life!</p>
</section>

<div class="brand brand--foot abs">BRISA<br>LAGOON</div>
<ul class="foot-links" style="left:358px">
  <li><a href="#">Home</a></li><li><a href="#">Our Products</a></li><li><a href="#">Our Works</a></li><li><a href="#">Contact Us</a></li>
</ul>
<ul class="foot-links" style="left:556px">
  <li><a href="#">Privacy Policy</a></li><li><a href="#">Terms &amp; Conditions</a></li><li><a href="#">Disclaimer</a></li>
</ul>
<div class="newsletter">
  <strong>Join our newsletter and get 20% discount!</strong>
  <div class="news-field"><span>Email</span>
    <svg width="22" height="16" viewBox="0 0 22 16" fill="none" stroke="#111" stroke-width="1.3"><rect x="1" y="1" width="20" height="14"/><path d="M1 1l10 8 10-8M1 15l7-7M21 15l-7-7"/></svg>
  </div>
</div>
<div class="abs foot-rule"></div>
<p class="abs copyright">Copyright © 2024 &nbsp; Brisa Lagoon . All rights reserved.</p>
<div class="socials" aria-label="Social links">
  <span style="background:#1877f2"></span><span style="background:#e6e6e6"></span><span style="background:#e60023"></span><span style="background:#c13584"></span><span style="background:#ff0000"></span>
</div>

</body>
</html>
```